Mental Health care Company in Washington DC

We are a new mental health care services provider in Washington DC. Please look at these sites.
https://brightwaterfamilysupport.com
https://www.quietharborinc.com
https://willowgate-dc.org/
https://www.tidepathdc.com
https://www.thelanternofdc.com

```html
<!DOCTYPE html>
<html lang="en">
<head>
<meta charset="UTF-8">
<title>Nuvio Health – Mental Wellness in Washington DC</title>
<link href="https://fonts.googleapis.com/css2?family=Poppins:wght@400;500;600;700&display=swap" rel="stylesheet">
<style>
:root{
  --navy:#0d1b3e;
  --orange:#f47c20;
  --teal:#5bbfc6;
  --ink:#1c2333;
  --text:#4a4f5c;
  --soft:#eef1f6;
  --line:#e3e6ec;
  --white:#ffffff;
}
*{box-sizing:border-box;margin:0;padding:0}
html,body{width:1200px;height:4556px;overflow:hidden}
body{position:relative;background:var(--white);font-family:'Poppins',sans-serif;color:var(--ink)}
.abs{position:absolute}
.eyebrow{font-size:14px;color:var(--teal);letter-spacing:.3px;text-transform:uppercase}
.divider{display:block;margin:8px auto 0;width:90px;height:10px}
.section-title{font-size:30px;font-weight:600;color:var(--navy)}
.center{left:0;width:1200px;text-align:center}
.btn{display:inline-flex;align-items:center;justify-content:center;gap:8px;background:var(--orange);color:#fff;border-radius:30px;font-weight:600;font-size:12px}

/* top bar */
.topbar{left:477px;top:0;width:723px;height:32px;background:var(--navy);clip-path:polygon(0 0,100% 0,100% 100%,22px 100%);color:#fff;font-size:10px;display:flex;align-items:center;gap:30px;padding-left:32px}
.topbar span{display:flex;align-items:center;gap:6px}
.topbar i{width:9px;height:9px;border-radius:50%;background:var(--orange);display:inline-block}
.topbar-edge{left:470px;top:0;width:22px;height:32px;background:var(--orange);clip-path:polygon(0 0,40% 0,100% 100%,60% 100%)}
.header{left:0;top:0;width:1200px;height:92px;border-bottom:1px solid var(--line)}
.logo{display:flex;align-items:center;gap:8px;font-size:30px;font-weight:500;color:var(--navy)}
.logo b{width:12px;height:12px;border-radius:50%;background:var(--orange)}
.nav{left:510px;top:52px;display:flex;gap:36px;font-size:13px;color:var(--ink)}
.nav .active{color:var(--orange);border-bottom:2px solid var(--orange);padding-bottom:4px}

/* hero */
.hero-media{left:0;top:92px;width:1200px;height:650px;background:linear-gradient(90deg,#2e3036 0%,#4d5157 45%,#8f959b 75%,#b8bdc2 100%)}
.hero-text{left:141px;top:212px;color:#fff}
.hero-text .kicker{font-size:22px;font-weight:500}
.hero-text h1{font-size:42px;font-weight:700;line-height:1.28;margin-top:6px}
.hero-text h1 em{font-style:normal;color:var(--teal)}
.hero-text h1 span{font-weight:500}
.hero-text p{font-size:15px;line-height:23px;margin-top:16px;width:400px;opacity:.95}
.hero-btn{left:141px;top:470px;width:200px;height:42px}
.scroll-dot{left:571px;top:700px;width:56px;height:56px;border-radius:50%;background:#fff;box-shadow:0 4px 14px rgba(0,0,0,.15);display:flex;align-items:center;justify-content:center}

/* about */
.about-ring{left:125px;top:800px;width:440px;height:425px;border-radius:50%;border:8px solid var(--orange);border-right-color:transparent;border-top-color:transparent;transform:rotate(20deg)}
.about-photo{left:136px;top:800px;width:430px;height:425px;border-radius:50%;background:radial-gradient(circle at 60% 40%,#d9e4ea,#9cb0bf 60%,#6d8396)}
.about-text{left:627px;top:818px;width:440px}
.about-text .eyebrow{display:flex;align-items:center;gap:10px}
.about-text h2{font-size:30px;font-weight:600;color:var(--navy);line-height:36px;margin-top:18px}
.about-text p{font-size:12.5px;line-height:22.6px;color:var(--text);margin-top:18px}
.about-btn{left:627px;top:1170px;width:195px;height:36px}

/* services */
.services-bg{left:0;top:1299px;width:1200px;height:571px;background:var(--soft)}
.service-card{top:1504px;width:295px;height:230px;background:#fff;border-radius:10px;overflow:hidden;box-shadow:0 6px 16px rgba(13,27,62,.06)}
.service-card .media{height:175px}
.service-card .label{height:55px;display:flex;align-items:center;justify-content:space-between;padding:0 24px;font-size:15px;font-weight:500}
.service-card.featured .label{background:var(--orange);color:#fff}
.dots{display:flex;gap:10px}
.dots i{width:16px;height:4px;border-radius:2px;background:#c7ccd6}
.dots i:first-child{background:var(--orange)}

/* testimonials */
.testi-head{left:141px;top:1958px}
.testi-head .eyebrow{display:flex;align-items:center;gap:10px}
.testi-head h2{margin-top:14px}
.arrow-btn{top:1983px;width:39px;height:37px;display:flex;align-items:center;justify-content:center}
.review{top:2075px;width:360px;height:254px;background:#fff;border-radius:8px;box-shadow:0 4px 18px rgba(13,27,62,.08);padding:12px}
.review-inner{border:1px solid var(--line);border-radius:6px;height:100%;padding:22px 24px}
.review h3{font-size:16px;font-weight:500;display:flex;justify-content:space-between;align-items:center}
.review .badge{width:30px;height:30px;border-radius:50%;background:#e8ecf2}
.stars{color:var(--orange);font-size:15px;letter-spacing:2px;margin-top:-4px}
.review hr{border:none;border-top:1px solid var(--line);margin:12px 0 16px}
.review p{font-size:13px;line-height:24px;color:var(--text)}
.quote{right:22px;bottom:-14px;font-size:120px;font-weight:700;line-height:1;color:var(--teal);height:60px;overflow:hidden}

/* team */
.team-bg{left:0;top:2444px;width:1200px;height:761px;background:var(--soft)}
.member{top:2651px;width:288px;height:339px;border-radius:10px}
.member-card{top:2947px;width:231px;height:131px;background:#fff;border-radius:8px;box-shadow:0 6px 18px rgba(13,27,62,.1);text-align:center;padding-top:26px}
.member-card h3{font-size:18px;font-weight:500}
.member-card small{display:block;font-size:12px;color:var(--text);margin-top:2px}
.socials{display:flex;justify-content:center;gap:14px;margin-top:14px}
.socials i{width:11px;height:11px;border-radius:50%;background:var(--orange)}

/* faq */
.footer{left:0;top:3700px;width:1200px;height:856px;background:var(--navy)}
.faq{left:141px;top:3410px;width:917px;background:#fff;border:1px solid var(--line)}
.faq-item{height:69px;border-bottom:1px solid var(--line);display:flex;align-items:center;justify-content:space-between;padding:0 24px 0 52px;font-size:15px;font-weight:500}
.faq-item:last-child{border-bottom:none}
.faq-item.open{height:145px;display:block;background:var(--soft);border-left:4px solid var(--orange);padding:32px 24px 0 48px}
.faq-item.open .row{display:flex;justify-content:space-between;align-items:center}
.faq-item.open p{font-size:12.5px;line-height:23px;color:var(--text);font-weight:400;margin-top:14px;width:760px}
.toggle{width:28px;height:28px;border-radius:50%;background:var(--navy);color:#fff;display:flex;align-items:center;justify-content:center;font-size:18px;line-height:1}
.toggle.minus{background:var(--orange)}

/* footer */
.footer-logo{left:0;top:4096px;width:1200px;display:flex;justify-content:center}
.footer-logo .logo{color:#fff;font-size:34px}
.fcol{top:4190px;color:#fff}
.fcol h4{font-size:18px;font-weight:500;padding-bottom:8px;position:relative}
.fcol h4:after{content:"";position:absolute;left:0;bottom:0;width:34px;height:2px;background:var(--orange)}
.fcol ul{list-style:none;margin-top:26px}
.fcol li{font-size:12.5px;line-height:31px;opacity:.9}
.contact-row{display:flex;align-items:center;gap:16px;font-size:12.5px;line-height:22px;margin-bottom:20px}
.contact-row i{flex:none;width:34px;height:34px;border-radius:50%;background:#fff;display:flex;align-items:center;justify-content:center}
.news p{font-size:12.5px;line-height:20px;margin-top:22px;opacity:.9}
.news .field{margin-top:18px;width:197px;height:36px;border-radius:20px;background:#fff;color:#8a8f99;font-size:11.5px;display:flex;align-items:center;justify-content:space-between;padding:0 18px}
.news .btn{margin-top:14px;width:197px;height:38px;font-size:13px}
.footer-rule{left:70px;top:4465px;width:1060px;height:1px;background:rgba(255,255,255,.2)}
.copyright{left:0;top:4484px;width:1200px;text-align:center;color:#fff;font-size:11.5px}
</style>
</head>
<body>

<!-- header -->
<header class="abs header">
  <div class="abs" style="left:141px;top:24px"><div class="logo"><b></b>Nuvio Health</div></div>
  <nav class="abs nav">
    <span class="active">Home</span><span>About Us</span><span>Services ⌄</span><span>Blog</span><span>FAQs</span>
  </nav>
  <a class="abs btn" style="left:952px;top:48px;width:106px;height:28px;font-size:11px">Contact Now</a>
</header>
<div class="abs topbar-edge"></div>
<div class="abs topbar">
  <span><i></i>Call now: (202) 555-0147</span>
  <span><i></i>Email: hello@nuviowellness.com</span>
  <span><i></i>Time: Mon - Sun, 08:30am to 05:30pm</span>
</div>

<!-- hero -->
<div class="abs hero-media" role="img" aria-label="Smiling doctor in a white coat with arms crossed in a bright clinic office"></div>
<svg class="abs" style="left:0;top:600px" width="1200" height="160" viewBox="0 0 1200 160">
  <path d="M0,27 C220,40 420,140 620,125 C820,110 980,10 1200,20 L1200,160 L0,160 Z" fill="#fff"/>
</svg>
<div class="abs hero-text">
  <div class="kicker">COMPASSIONATE</div>
  <h1>MENTAL <em>WELLNESS</em> IN<br><span>WASHINGTON DC</span></h1>
  <p>Evidence-based care tailored to your needs. Where clinical expertise meets your unique needs</p>
</div>
<a class="abs btn hero-btn">
  <svg width="14" height="14" viewBox="0 0 14 14"><rect x="1" y="2.5" width="12" height="10.5" rx="2" fill="none" stroke="#fff" stroke-width="1.6"/><path d="M1 6h12M4 1v3M10 1v3" stroke="#fff" stroke-width="1.6"/></svg>
  BOOK APPOINTMENT
</a>
<div class="abs scroll-dot">
  <svg width="20" height="26" viewBox="0 0 20 26"><path d="M10 2v21M3 16l7 7 7-7" fill="none" stroke="#f47c20" stroke-width="2"/></svg>
</div>

<!-- about -->
<div class="abs about-ring"></div>
<div class="abs about-photo" role="img" aria-label="Doctor shaking hands with a patient during a consultation"></div>
<div class="abs about-text">
  <div class="eyebrow">Who We Are
    <svg width="70" height="12" viewBox="0 0 70 12"><path d="M6 0v12M0 6h12" stroke="#f47c20" stroke-width="2"/><path d="M20 6h50" stroke="#dfe3ea"/></svg>
  </div>
  <h2>A Trusted Mental Health<br>Partner In DC</h2>
  <p>Lorem Ipsum is simply dummy text of the printing and typesetting industry. Lorem Ipsum has been the industry's standard dummy text ever since the 1500s, when an unknown printer took a galley of type and scrambled it to make a type specimen book. It has survived not only five centuries, but also the leap into electronic typesetting, remaining essentially unchanged. It was popularised in the 1960s with the release of lettering sheets containing Lorem Ipsum passages, and more recently with desktop publishing software like page layout tools including versions of Lorem Ipsum</p>
</div>
<a class="abs btn about-btn">Learn More About Us</a>

<!-- services -->
<div class="abs services-bg"></div>
<div class="abs center" style="top:1386px">
  <div class="eyebrow">Our Core Services</div>
  <svg class="divider" viewBox="0 0 90 10"><path d="M0 5h38M52 5h38" stroke="#cfd5de"/><path d="M45 0v10M40 5h10" stroke="#f47c20" stroke-width="2"/></svg>
  <h2 class="section-title" style="margin-top:10px">Transformative Services For Real Results</h2>
</div>
<div class="abs service-card" style="left:138px">
  <div class="media" role="img" aria-label="Woman talking with a therapist in an individual session" style="background:linear-gradient(135deg,#e7ddd5,#c9b3a4)"></div>
  <div class="label">Individual Therapy<svg width="18" height="18" viewBox="0 0 18 18"><path d="M3 15L15 3M6 3h9v9" fill="none" stroke="#1c2333" stroke-width="1.4"/></svg></div>
</div>
<div class="abs service-card featured" style="left:452px">
  <div class="media" role="img" aria-label="Group of smiling healthcare professionals in white coats" style="background:linear-gradient(135deg,#cfd6dc,#8e9aa5)"></div>
  <div class="label">Support Groups<svg width="22" height="14" viewBox="0 0 22 14"><path d="M0 7h20M14 1l6 6-6 6" fill="none" stroke="#fff" stroke-width="1.6"/></svg></div>
</div>
<div class="abs service-card" style="left:767px">
  <div class="media" role="img" aria-label="Nurse counseling an older patient at a computer" style="background:linear-gradient(135deg,#3f6e96,#9fbdd4)"></div>
  <div class="label">Counseling<svg width="18" height="18" viewBox="0 0 18 18"><path d="M3 15L15 3M6 3h9v9" fill="none" stroke="#1c2333" stroke-width="1.4"/></svg></div>
</div>
<div class="abs dots" style="left:554px;top:1781px"><i></i><i></i><i></i><i></i></div>

<!-- testimonials -->
<div class="abs testi-head">
  <div class="eyebrow">Client Testimonials
    <svg width="70" height="12" viewBox="0 0 70 12"><path d="M6 0v12M0 6h12" stroke="#f47c20" stroke-width="2"/><path d="M20 6h50" stroke="#dfe3ea"/></svg>
  </div>
  <h2 class="section-title">A Trusted Mental Health Partner In DC</h2>
</div>
<div class="abs arrow-btn" style="left:970px;background:var(--orange)"><svg width="10" height="14" viewBox="0 0 10 14"><path d="M8 1L2 7l6 6" fill="none" stroke="#fff" stroke-width="2"/></svg></div>
<div class="abs arrow-btn" style="left:1023px;background:var(--navy)"><svg width="10" height="14" viewBox="0 0 10 14"><path d="M2 1l6 6-6 6" fill="none" stroke="#fff" stroke-width="2"/></svg></div>

<div class="abs review" style="left:141px">
  <div class="review-inner">
    <h3>Tara Whitlow<span class="badge"></span></h3>
    <div class="stars">★★★★★</div><hr>
    <p>Lorem Ipsum is simply dummy text of the printing and typesetting industry. Lorem Ipsum has been the industry's standard dummy text ever since the 1500s.</p>
  </div>
  <div class="abs quote">”</div>
</div>
<div class="abs review" style="left:530px">
  <div class="review-inner">
    <h3>Marcus Delano<span class="badge"></span></h3>
    <div class="stars">★★★★★</div><hr>
    <p>Lorem Ipsum is simply dummy text of the printing and typesetting industry. Lorem Ipsum has been the industry's standard dummy text ever since the 1500s.</p>
  </div>
  <div class="abs quote">”</div>
</div>
<div class="abs review" style="left:921px">
  <div class="review-inner">
    <h3>J. Hensley<span class="badge"></span></h3>
    <div class="stars">★★★★★</div><hr>
    <p>Lorem Ipsum is simply dummy text of the printing and typesetting industry. Lorem Ipsum has been the industry's standard dummy text ever since the 1500s.</p>
  </div>
</div>

<!-- team -->
<div class="abs team-bg"></div>
<div class="abs center" style="top:2531px">
  <div class="eyebrow">Meet Our Team</div>
  <svg class="divider" viewBox="0 0 90 10"><path d="M0 5h38M52 5h38" stroke="#cfd5de"/><path d="M45 0v10M40 5h10" stroke="#f47c20" stroke-width="2"/></svg>
  <h2 class="section-title" style="margin-top:10px">Meet The Minds Behind The Mission</h2>
</div>
<div class="abs member" style="left:141px;background:linear-gradient(180deg,#e4e5e7,#c8cacd)" role="img" aria-label="Male doctor with stethoscope, arms crossed"></div>
<div class="abs member" style="left:458px;background:linear-gradient(180deg,#c9b9a3,#e6e2dc)" role="img" aria-label="Female doctor in white coat standing in an office"></div>
<div class="abs member" style="left:774px;background:linear-gradient(180deg,#f1f2f4,#d6dade)" role="img" aria-label="Smiling female clinician in blue scrubs and white coat"></div>
<div class="abs member-card" style="left:170px"><h3>Owen Marsh</h3><small>Anxiety Specialist</small><div class="socials"><i></i><i></i><i></i><i></i></div></div>
<div class="abs member-card" style="left:486px"><h3>Lena Ortiz</h3><small>Trauma Expert</small><div class="socials"><i></i><i></i><i></i><i></i></div></div>
<div class="abs member-card" style="left:802px"><h3>Grace Fulton</h3><small>Group Therapy Lead</small><div class="socials"><i></i><i></i><i></i><i></i></div></div>
<div class="abs dots" style="left:554px;top:3113px"><i></i><i></i><i></i><i></i></div>

<!-- faq -->
<div class="abs center" style="top:3294px">
  <div class="eyebrow">FAQs</div>
  <svg class="divider" viewBox="0 0 90 10"><path d="M0 5h38M52 5h38" stroke="#cfd5de"/><path d="M45 0v10M40 5h10" stroke="#f47c20" stroke-width="2"/></svg>
  <h2 class="section-title" style="margin-top:10px">Frequently Asked Questions</h2>
</div>

<!-- footer background -->
<footer class="abs footer"></footer>
<svg class="abs" style="left:0;top:3700px" width="1200" height="340" viewBox="0 0 1200 340">
  <path d="M0,0 L1200,0 L1200,240 C1120,150 1000,190 860,250 C720,310 560,320 430,290 C260,250 120,120 0,30 Z" fill="#fff"/>
</svg>

<div class="abs faq">
  <div class="faq-item">Who Is Your Primary Target Audience?<span class="toggle">+</span></div>
  <div class="faq-item">What Are The Top 3 Actions You Want Visitors To Take On The Website?<span class="toggle">+</span></div>
  <div class="faq-item open">
    <div class="row">Do You Have Existing Branding Elements To Incorporate, Or Should The Design Start Fresh?<span class="toggle minus">−</span></div>
    <p>Lorem Ipsum is simply dummy text of the printing and typesetting industry. Lorem Ipsum has been the industry's standard dummy text ever since the 1500s.</p>
  </div>
  <div class="faq-item">Are There Any Specific Services Or Features That Must Be Highlighted Or Integrated?<span class="toggle">+</span></div>
  <div class="faq-item">What Is Your Preferred Timeline And Budget For Launching The Website?<span class="toggle">+</span></div>
</div>

<div class="abs footer-logo"><div class="logo"><b></b>Nuvio Health</div></div>

<div class="abs fcol" style="left:141px">
  <h4>Quick Links</h4>
  <ul><li>Home</li><li>About Us</li><li>Services</li><li>Blog</li><li>FAQs</li></ul>
</div>
<div class="abs fcol" style="left:337px">
  <h4>Useful Links</h4>
  <ul><li>Contact Us</li><li>Privacy Policy</li><li>Terms &amp; Conditions</li></ul>
</div>
<div class="abs fcol" style="left:544px">
  <h4>Contact Us</h4>
  <div style="margin-top:26px">
    <div class="contact-row"><i><svg width="14" height="16" viewBox="0 0 14 16"><path d="M7 15s5-5 5-9a5 5 0 0 0-10 0c0 4 5 9 5 9z" fill="none" stroke="#f47c20" stroke-width="1.6"/><circle cx="7" cy="6" r="1.8" fill="#f47c20"/></svg></i><span>123, Lorem Ipsum is simply<br>dummy text of the printing</span></div>
    <div class="contact-row"><i><svg width="14" height="14" viewBox="0 0 14 14"><path d="M3 1l2 3-1.5 1.5a8 8 0 0 0 5 5L10 9l3 2-1 2.5C6 13 1 8 .5 2z" fill="#f47c20"/></svg></i><span>Phone: (202)-555-0147</span></div>
    <div class="contact-row"><i><svg width="16" height="12" viewBox="0 0 16 12"><rect x="1" y="1" width="14" height="10" rx="1" fill="none" stroke="#f47c20" stroke-width="1.5"/><path d="M1 1l7 6 7-6" fill="none" stroke="#f47c20" stroke-width="1.5"/></svg></i><span>info@nuviomentalhealth.com</span></div>
  </div>
</div>
<div class="abs fcol news" style="left:853px">
  <h4>Newsletter</h4>
  <p>Join our subscribers list to get the<br>latest news &amp; special offers.</p>
  <div class="field">Enter your email<svg width="16" height="12" viewBox="0 0 16 12"><rect x="1" y="1" width="14" height="10" rx="1" fill="none" stroke="#8a8f99" stroke-width="1.2"/><path d="M1 1l7 6 7-6" fill="none" stroke="#8a8f99" stroke-width="1.2"/></svg></div>
  <a class="btn">SUBSCRIBE NOW</a>
</div>
<div class="abs footer-rule"></div>
<div class="abs copyright">Copyright © 2025 Nuvio Mental Health | All Rights Reserved.</div>

</body>
</html>
```